Building company buisness cards

We are looking for a sharp modern new look for our business cards.
We are a New Zealand based company that specialises in house and land packages.
We have attached a photo of the current logo and would like to see if it can be improved somehow if needed.
We are open to any colours but we have chosen green at this stage.
Feel free to change the font and make the logo smarter looking.
Play with the colours and see what looks best.

We want a card that looks so good know one will want to throw it away!

Target Market(s)

Home buyers

Industry/Entity Type

Building

Contact Information for Business Card

Derek Tolvane
0217394062
dtolvane@quillmarkhomesteads.co.nz
quillmarkhomesteads.co.nz

Font styles to use
Serif
Sans Serif

Colors

Designer to choose colors to be used in the design.

Requirements
Must have
• Logo and company name on one side, details on the other side
Nice to have
• Color codes for the original green are HEX #4a8028, RGB(74,128,40), CMYK(42,0,69,50)
• Round corners, Raised and/or spot UV

```html
<!DOCTYPE html>
<html lang="en">
<head>
<meta charset="utf-8">
<title>Quillmark Homesteads – Business Cards</title>
<link rel="stylesheet" href="https://fonts.googleapis.com/css2?family=Open+Sans:wght@400;600&display=swap">
<style>
  :root {
    --brand-green: #4a8028;
    --card-white: #ffffff;
    --ink-grey: #4a4a4a;
    --divider: #c9c9c9;
    --backdrop: #e6e3e0;
  }
  * { box-sizing: border-box; margin: 0; padding: 0; }
  html, body {
    width: 1200px; height: 997px; overflow: hidden;
    background: var(--backdrop);
    font-family: "Open Sans", Arial, sans-serif;
  }
  .canvas { position: relative; width: 1200px; height: 997px; }

  .card {
    position: absolute;
    width: 560px; height: 320px;
    background: var(--card-white);
    border-radius: 6px;
    overflow: hidden;
    box-shadow: 0 2px 6px rgba(0,0,0,0.08);
  }
  .card--details { left: 80px; top: 150px; }
  .card--brand { left: 560px; top: 520px; }

  .card__band { position: absolute; inset: 0; width: 100%; height: 100%; }

  .company-name {
    color: var(--brand-green);
    font-weight: 600;
    line-height: 1;
    white-space: nowrap;
  }
  .card--details .company-name {
    position: absolute; left: 40px; top: 70px;
    font-size: 24px;
    display: flex; align-items: center; gap: 10px;
  }
  .company-name__dot {
    width: 12px; height: 12px; background: var(--brand-green); border-radius: 50%; flex: none;
  }

  .contact { position: absolute; left: 40px; top: 190px; }
  .contact__name {
    color: var(--brand-green); font-weight: 600; font-size: 17px; margin-bottom: 8px;
  }
  .contact__line {
    display: flex; align-items: center; gap: 8px;
    color: var(--ink-grey); font-size: 13px; line-height: 21px;
  }
  .contact__icon { width: 11px; height: 11px; flex: none; }

  .card--brand .brand-lockup {
    position: absolute; inset: 0;
    display: flex; flex-direction: column; align-items: center; justify-content: center;
  }
  .card--brand .company-name { font-size: 32px; }
  .brand-lockup__rule {
    width: 60px; height: 1px; background: var(--divider); margin-top: 18px;
  }
</style>
</head>
<body>
<main class="canvas">
  <section class="card card--details" aria-label="Business card, contact side">
    <svg class="card__band" viewBox="0 0 560 320" preserveAspectRatio="none" aria-hidden="true">
      <path d="M430 0 C470 120 420 240 330 320 L560 320 L560 0 Z" fill="var(--brand-green)"/>
    </svg>

    <div class="company-name"><span class="company-name__dot"></span>Quillmark Homesteads</div>

    <div class="contact">
      <p class="contact__name">Derek Tolvane</p>
      <p class="contact__line">
        <svg class="contact__icon" viewBox="0 0 12 12" aria-hidden="true"><path d="M2 1 L4.5 1 L5.5 3.5 L4 4.6 C4.8 6.3 5.7 7.2 7.4 8 L8.5 6.5 L11 7.5 L11 10 C6 11 1 6 2 1 Z" fill="var(--brand-green)"/></svg>
        0217394062
      </p>
      <p class="contact__line">
        <svg class="contact__icon" viewBox="0 0 12 12" aria-hidden="true"><rect x="0.5" y="2" width="11" height="8" fill="var(--brand-green)"/><path d="M0.5 2 L6 6.5 L11.5 2" stroke="#fff" fill="none"/></svg>
        dtolvane@quillmarkhomesteads.co.nz
      </p>
      <p class="contact__line">
        <svg class="contact__icon" viewBox="0 0 12 12" aria-hidden="true"><circle cx="6" cy="6" r="5.5" fill="var(--brand-green)"/><path d="M0.5 6 H11.5 M6 0.5 C3 3 3 9 6 11.5 M6 0.5 C9 3 9 9 6 11.5" stroke="#fff" stroke-width="0.8" fill="none"/></svg>
        www.quillmarkhomesteads.co.nz
      </p>
    </div>
  </section>

  <section class="card card--brand" aria-label="Business card, brand side">
    <div class="brand-lockup">
      <div class="company-name">Quillmark Homesteads</div>
      <span class="brand-lockup__rule"></span>
    </div>
  </section>
</main>
</body>
</html>
```